Lip Balm Label Design

Design a label for a Lavender-Mint lip balm. We make high-quality natural essential oil products. Please use the old label as an example of what exists. The label should include purple. The final design should be eye-catching and distinct. The file should be in an AI file.

Here is the information that should be included on the label:
1) ingredients:Theobroma Cacao (Cocoa) Seed Butter, Theobroma grandiflorum Ultra Refined Butter, beesewax, Calendula Officinalis Flower Oil, Prunus Amygdalus Dulcis (Sweet Almond) Oil, cetyl alcohol and Tocopherol. Lavandula Angustifolia (Lavender) Oil and Mentha Piperita (Peppermint) Oil.

2) www.kelsoroothaven.com

3) Brand name and logo: K. Elso Aromatherapy (logo is attached- you can use with form)

```html
<!DOCTYPE html>
<html lang="en">
<head>
<meta charset="utf-8">
<title>K. Elso Aromatherapy – Lavender-Mint Lip Balm Label</title>
<link rel="stylesheet" href="https://fonts.googleapis.com/css2?family=Marcellus&family=Arimo:wght@400;700&display=swap">
<style>
  :root {
    --page: #fdfbf4;
    --label: #fbf1f2;
    --label-edge: #f6e3e6;
    --plum: #b04f8e;
    --plum-soft: #c97bb0;
    --blush: #f3b3b6;
    --ink-soft: #d58fbd;
    --ink-dark: #555555;
    --tag-text: #ffffff;
  }
  * { margin: 0; padding: 0; box-sizing: border-box; }
  html, body { width: 1200px; height: 909px; overflow: hidden; }
  body {
    background: var(--page);
    display: flex;
    align-items: center;
    justify-content: center;
  }
  .label {
    width: 1080px;
    height: 300px;
    background: linear-gradient(180deg, var(--label) 0%, #fff 50%, var(--label) 100%);
    border: 1px solid var(--label-edge);
    display: grid;
    grid-template-columns: 150px 380px 400px 150px;
    align-items: stretch;
    overflow: hidden;
  }
  .leaf-art {
    height: 100%;
    width: 100%;
    background: linear-gradient(135deg, var(--blush) 0%, var(--plum-soft) 45%, var(--plum) 100%);
    opacity: .85;
  }
  .leaf-art--end {
    background: linear-gradient(315deg, var(--blush) 0%, var(--plum-soft) 45%, var(--plum) 100%);
  }
  .front {
    padding: 0 30px;
    display: flex;
    flex-direction: column;
    gap: 6px;
    justify-content: center;
    position: relative;
  }
  .brand {
    font-family: "Marcellus", serif;
    color: var(--plum);
    font-size: 54px;
    line-height: 1;
    letter-spacing: 1px;
    display: flex;
    align-items: center;
    gap: 12px;
  }
  .brand-dot {
    width: 14px; height: 14px;
    border-radius: 50%;
    background: var(--plum);
    flex: none;
  }
  .brand-sub {
    font-family: "Marcellus", serif;
    color: var(--plum);
    font-size: 15px;
    letter-spacing: 2px;
    text-transform: uppercase;
    padding-left: 26px;
  }
  .flavour {
    font-family: "Marcellus", serif;
    color: var(--plum-soft);
    font-size: 32px;
    letter-spacing: 2px;
    text-transform: uppercase;
    margin-top: 18px;
  }
  .net-weight {
    font-family: "Marcellus", serif;
    color: var(--ink-dark);
    font-size: 17px;
    position: absolute;
    left: 30px;
    bottom: 16px;
  }
  .back {
    padding: 0 20px;
    display: flex;
    flex-direction: column;
    justify-content: center;
    gap: 10px;
  }
  .back-head {
    display: flex;
    align-items: center;
    gap: 14px;
  }
  .back-flavour {
    font-family: "Marcellus", serif;
    color: var(--plum-soft);
    font-size: 20px;
    letter-spacing: 1.5px;
    text-transform: uppercase;
  }
  .product-tag {
    font-family: "Marcellus", serif;
    color: var(--tag-text);
    background: var(--plum-soft);
    font-size: 16px;
    letter-spacing: 1px;
    padding: 3px 10px;
    border-radius: 3px;
  }
  .ingredients {
    font-family: "Arimo", sans-serif;
    color: var(--ink-soft);
    font-size: 14px;
    line-height: 1.5;
    text-align: justify;
  }
  .ingredients strong { color: var(--plum-soft); font-weight: 700; }
  .website {
    font-family: "Arimo", sans-serif;
    color: var(--plum);
    font-size: 14px;
    font-weight: 700;
    letter-spacing: .5px;
  }
</style>
</head>
<body>
  <main class="label">
    <div class="leaf-art" role="img" aria-label="Decorative pink and plum leaf sprays"></div>

    <section class="front">
      <div class="brand"><span class="brand-dot"></span>K. Elso</div>
      <div class="brand-sub">Aromatherapy</div>
      <div class="flavour">Lavender-Mint</div>
      <div class="net-weight">0.15 Oz</div>
    </section>

    <section class="back">
      <div class="back-head">
        <span class="back-flavour">Lavender-Mint</span>
        <span class="product-tag">LIP BALM</span>
      </div>
      <p class="ingredients"><strong>INGREDIENTS:</strong> Theobroma Cacao (Cocoa) Seed Butter, Theobroma grandiflorum Ultra Refined Butter, beesewax, Calendula Officinalis Flower Oil, Prunus Amygdalus Dulcis (Sweet Almond) Oil, cetyl alcohol and Tocopherol. Lavandula Angustifolia (Lavender) Oil and Mentha Piperita (Peppermint) Oil.</p>
      <p class="website">www.kelsoroothaven.com</p>
    </section>

    <div class="leaf-art leaf-art--end" role="img" aria-label="Decorative plum leaf accent"></div>
  </main>
</body>
</html>
```